Business Cards Design for the electrical wholesaler: clean bold dynamic :)

We need a business card design that would follow our latest brand guidelines. As an electrical wholesaler we want to bring a fresh look and feel into the industry. The design should be clean bold and dynamic. It should come alive with the renewed energy of our green colour. Our grey colour should keep things balanced and complement the notion of maturity and responsibility. We employ Lato as a corporate font however are not bound by this font and we’re open to interpretation here.

Target Market(s)

Electrical contractors

Industry/Entity Type

Business

Contact Information for Business Card

Logo
Name & Surname: Halyna Dorosh
Job Title: Director of Marketing
Email: halya.dorosh@quillmail.example
Cell phone: XXX.XXX.XXXX
Address: 20517 - 87 Ave. Edmonton, AB, Canada. T6K 4N8
Business Phone: 780.555.0184
Website: www.brovix.example

Font styles to use
Other font styles liked:
• Lato

Requirements
Must have
• Logo & website
Nice to have
• Brand elements - some of them you may find in the attached Brand Guidelines (e.g. three lines on the background signifying "W")

```html
<!DOCTYPE html>
<html lang="en">
<head>
<meta charset="utf-8">
<title>Brovix Business Cards</title>
<link rel="stylesheet" href="https://fonts.googleapis.com/css2?family=Roboto:wght@300;400;500;700&display=swap">
<style>
  :root {
    --stage: #e9e7e3;
    --charcoal: #232323;
    --charcoal-edge: #1b1b1b;
    --paper: #f7f7f7;
    --green: #7ac70c;
    --ink: #2a2a2a;
    --ink-soft: #444;
    --white: #ffffff;
  }
  * { box-sizing: border-box; margin: 0; padding: 0; }
  html, body {
    width: 1200px; height: 800px; overflow: hidden;
    background: var(--stage);
    font-family: "Roboto", Arial, sans-serif;
  }
  .stage {
    position: relative; width: 1200px; height: 800px;
    display: flex; align-items: center; justify-content: center; gap: 60px;
  }
  .card {
    position: relative; width: 525px; height: 300px;
    border-radius: 4px; overflow: hidden;
    box-shadow: 0 10px 30px rgba(0,0,0,.18);
  }
  /* Front */
  .card-front {
    background: var(--charcoal);
    display: flex; flex-direction: column; align-items: center; justify-content: center;
  }
  .brand {
    display: flex; align-items: center; gap: 14px;
    color: var(--white); font-weight: 400; letter-spacing: -0.5px;
  }
  .brand-mark { width: 30px; height: 30px; background: var(--green); }
  .card-front .brand { font-size: 62px; }
  .card-front .site {
    position: absolute; bottom: 40px; right: 50px;
    color: var(--green); font-size: 13px; letter-spacing: 3px;
  }
  /* Back */
  .card-back { display: flex; background: var(--paper); }
  .back-panel {
    width: 46%; background: var(--charcoal);
    display: flex; align-items: center; justify-content: center;
  }
  .back-panel .brand { flex-direction: column; gap: 12px; font-size: 50px; }
  .back-panel .brand-mark { width: 40px; height: 40px; }
  .back-info { position: relative; flex: 1; padding: 52px 24px 0 34px; }
  .pointer {
    position: absolute; left: 0; top: 48px; width: 26px; height: 24px;
  }
  .person-name { font-weight: 300; font-size: 21px; color: var(--ink); }
  .person-role { font-weight: 700; font-size: 12px; color: var(--ink); margin-top: 2px; }
  .contact-list { list-style: none; margin-top: 48px; font-size: 12px; color: var(--ink-soft); }
  .contact-list li { display: flex; gap: 8px; line-height: 1.35; margin-bottom: 2px; }
  .contact-list svg { flex: none; width: 11px; height: 12px; margin-top: 2px; }
  .back-site {
    position: absolute; left: 34px; bottom: 24px;
    font-size: 13px; letter-spacing: 1.5px; color: var(--ink);
  }
  .back-site .accent { color: var(--green); font-weight: 500; }
</style>
</head>
<body>
<main class="stage">
  <section class="card card-front" aria-label="Card front">
    <div class="brand"><span class="brand-mark"></span>brovix</div>
    <p class="site">www.brovix.example</p>
  </section>

  <section class="card card-back" aria-label="Card back">
    <div class="back-panel">
      <div class="brand"><span class="brand-mark"></span>brovix</div>
    </div>
    <div class="back-info">
      <svg class="pointer" viewBox="0 0 26 24" aria-hidden="true"><polygon points="0,0 26,12 0,24" fill="#7ac70c"/></svg>
      <h1 class="person-name">Oskar Lindqvist</h1>
      <p class="person-role">Manager Finance</p>
      <ul class="contact-list">
        <li>
          <svg viewBox="0 0 12 14" aria-hidden="true"><path d="M6 0a5 5 0 0 0-5 5c0 3.5 5 9 5 9s5-5.5 5-9a5 5 0 0 0-5-5zm0 7a2 2 0 1 1 0-4 2 2 0 0 1 0 4z" fill="#7ac70c"/></svg>
          <span>20517 87 Ave. Edmonton, AB<br>T6K 4N8</span>
        </li>
        <li>
          <svg viewBox="0 0 10 14" aria-hidden="true"><rect x="1" y="0.5" width="8" height="13" rx="1.5" fill="none" stroke="#7ac70c" stroke-width="1.4"/><circle cx="5" cy="11" r="0.9" fill="#7ac70c"/></svg>
          <span>780.555.0184</span>
        </li>
        <li>
          <svg viewBox="0 0 14 11" aria-hidden="true"><rect x="0.7" y="0.7" width="12.6" height="9.6" rx="1" fill="none" stroke="#7ac70c" stroke-width="1.4"/><polyline points="1,1.5 7,6 13,1.5" fill="none" stroke="#7ac70c" stroke-width="1.4"/></svg>
          <span>hello@brovix.example</span>
        </li>
      </ul>
      <p class="back-site">www.<span class="accent">brovix</span>.example</p>
    </div>
  </section>
</main>
</body>
</html>
```